Mental Health care Company in Washington DC

We are a new mental health care services provider in Washington DC. Please look at these sites.
https://brightwaterfamilysupport.com
https://www.quietharborinc.com
https://willowgate-dc.org/
https://www.tidepathdc.com
https://www.thelanternofdc.com

```html
<!DOCTYPE html>
<html lang="en">
<head>
<meta charset="utf-8">
<title>Calder Health Services – Mental Wellness in DC</title>
<link href="https://fonts.googleapis.com/css2?family=Plus+Jakarta+Sans:wght@400;500;600;700;800&display=swap" rel="stylesheet">
<style>
:root{
  --navy:#0d1f44;
  --navy-2:#13294f;
  --orange:#f47f20;
  --orange-soft:#fde8d5;
  --teal:#5cc8c9;
  --ink:#1f2a3c;
  --muted:#5d6472;
  --gray-bg:#f3f3f4;
  --gray-bg-2:#ececec;
  --line:#e6e6e9;
  --white:#ffffff;
}
*{box-sizing:border-box;margin:0;padding:0}
html,body{width:1200px;height:4488px;overflow:hidden}
body{font-family:"Plus Jakarta Sans",Arial,sans-serif;color:var(--ink);background:var(--white);position:relative}
.abs{position:absolute}
a{color:inherit;text-decoration:none}

/* top bar + header */
.topbar{left:0;top:0;width:1200px;height:28px;background:var(--navy);color:#fff;font-size:11px;display:flex;align-items:center;justify-content:center;letter-spacing:.2px}
.header{left:0;top:28px;width:1200px;height:78px;background:#fff}
.brand{display:flex;align-items:center;gap:8px}
.brand-dot{width:12px;height:12px;border-radius:50%;background:var(--orange)}
.brand-name{font-size:30px;font-weight:500;color:var(--navy);line-height:1}
.brand-sub{font-size:10px;letter-spacing:6px;color:var(--navy);font-weight:500;margin-top:2px;padding-left:22px}
.nav{left:413px;top:58px;display:flex;gap:28px;font-size:13px;font-weight:500;color:var(--ink)}
.nav .caret::after{content:"";display:inline-block;width:4px;height:4px;border-right:1.3px solid var(--ink);border-bottom:1.3px solid var(--ink);transform:rotate(45deg);margin-left:5px;position:relative;top:-3px}
.btn-appt{left:866px;top:50px;width:191px;height:35px;border-radius:18px;background:var(--orange);color:#fff;font-size:13px;font-weight:600;display:flex;align-items:center;justify-content:center}

/* hero */
.hero{left:0;top:106px;width:1200px;height:660px;overflow:hidden}
.hero-photo{position:absolute;inset:0;background:linear-gradient(100deg,#233a5a 0%,#3b5571 35%,#8a94a0 60%,#c7c3bd 80%,#e4e0da 100%)}
.hero-shade{position:absolute;inset:0;background:linear-gradient(90deg,rgba(13,31,68,.55) 0%,rgba(13,31,68,.15) 55%,rgba(13,31,68,0) 100%)}
.hero-title{left:141px;top:118px;color:#fff;font-size:49px;font-weight:800;line-height:1.1;letter-spacing:.3px}
.hero-title .dot{color:var(--teal)}
.hero-sub{left:141px;top:254px;color:#fff;font-size:14px;line-height:1.85}
.btn-start{left:141px;top:340px;width:139px;height:33px;border-radius:17px;background:var(--teal);color:var(--navy);font-size:12.5px;font-weight:600;display:flex;align-items:center;justify-content:center}
.hero-wave{position:absolute;left:0;top:0}

/* section labels */
.label{display:flex;align-items:center;gap:8px;font-size:16px;font-weight:600;color:var(--navy);letter-spacing:.3px}
.label .accent{color:var(--orange)}
.label .mark{display:flex;align-items:center;gap:4px}
.label .mark i{display:block;width:8px;height:8px;border-radius:50%;background:var(--orange)}
.label .mark b{display:block;width:78px;height:1px;background:#b9bec8}
.center{left:0;width:1200px;justify-content:center}

/* about */
.about-img-main{left:141px;top:836px;width:355px;height:265px;background:linear-gradient(160deg,#9fb3c6,#5d7892 55%,#dfe6ec)}
.about-img-small{left:402px;top:969px;width:157px;height:163px;background:linear-gradient(160deg,#d7e1e8,#7e97ab 60%,#c8d3dc);border:4px solid #fff}
.about-title{left:608px;top:838px;font-size:29px;font-weight:700;color:var(--navy);line-height:1.25}
.about-title span{color:var(--orange)}
.about-text{left:608px;top:925px;width:400px;font-size:11px;line-height:1.65;color:var(--ink)}
.about-text p{margin-bottom:9px}
.read-link{font-size:12px;font-weight:600;display:flex;align-items:center;gap:6px;text-decoration:underline}
.read-link.navy{color:var(--navy)}
.read-link.orange{color:var(--orange)}

/* services */
.services-bg{left:0;top:1220px;width:1200px;height:610px;background:var(--gray-bg)}
.h2{font-size:27px;font-weight:700;color:var(--navy);text-align:center}
.h2 span{color:var(--orange)}
.svc-card{top:1385px;width:289px;height:367px;background:#fff;border-radius:8px;overflow:hidden;box-shadow:0 3px 12px rgba(13,31,68,.06);text-align:center}
.svc-img{height:206px}
.svc-icon{position:absolute;left:50%;top:178px;width:54px;height:54px;margin-left:-27px;border-radius:50%;border:4px solid #fff;display:flex;align-items:center;justify-content:center}
.svc-title{margin-top:42px;font-size:15px;font-weight:600;color:var(--navy)}
.svc-text{margin:8px auto 0;width:210px;font-size:11px;line-height:1.55;color:var(--muted)}
.svc-card .read-link{justify-content:center;margin-top:22px}

/* why */
.why-circle{left:441px;top:1997px;width:320px;height:320px;border-radius:50%;border:7px solid var(--orange);padding:6px;background:#fff}
.why-circle div{width:100%;height:100%;border-radius:50%;background:radial-gradient(circle at 50% 50%,#e8c7b8 0%,#b9a4a0 40%,#7e8da2 100%)}
.why-item{width:260px}
.why-item h4{font-size:15px;font-weight:600;color:var(--navy);margin-bottom:6px}
.why-item p{font-size:11px;line-height:1.6;color:var(--muted)}
.why-item.right{text-align:right}
.num{width:26px;height:26px;border-radius:50%;color:#fff;font-size:11px;font-weight:600;display:flex;align-items:center;justify-content:center}
.num.n{background:var(--navy)}
.num.o{background:var(--orange)}

/* stats */
.stats{left:141px;top:2505px;width:916px;height:141px;background:var(--orange);border-radius:10px;color:#fff;display:flex}
.stat{flex:1;display:flex;flex-direction:column;align-items:center;justify-content:center;position:relative}
.stat + .stat::before{content:"";position:absolute;left:0;top:30px;bottom:30px;width:1px;background:rgba(255,255,255,.55)}
.stat strong{font-size:40px;font-weight:700;line-height:1}
.stat span{font-size:13px;margin-top:10px}

/* blog */
.blog-track{left:141px;top:2782px;width:983px;height:317px;overflow:hidden}
.blog-card{position:absolute;top:0;width:230px;height:317px;background:#fff;box-shadow:0 3px 12px rgba(13,31,68,.08)}
.blog-card.feature{background:var(--navy);color:#fff;padding:42px 16px 0}
.blog-card.feature h3{font-size:15px;line-height:1.5;font-weight:600;margin-bottom:12px}
.blog-card.feature p{font-size:10.5px;line-height:1.6;color:#dfe3ea}
.blog-card.feature .read-link{position:absolute;left:16px;bottom:26px}
.blog-img{height:159px}
.blog-body{padding:16px 15px 0}
.blog-body h3{font-size:15px;font-weight:600;color:var(--navy);margin-bottom:6px}
.blog-body p{font-size:10.5px;line-height:1.6;color:var(--muted)}
.blog-card .blog-body + .read-link{position:absolute;left:15px;bottom:26px}
.blog-fade{position:absolute;right:0;top:0;width:90px;height:317px;background:linear-gradient(90deg,rgba(255,255,255,0),#fff)}
.arrow{font-size:22px;color:var(--navy);line-height:1}

/* insurance */
.table{left:141px;top:3211px;width:916px;border:1px solid var(--line);border-radius:6px;overflow:hidden;border-collapse:collapse;font-size:11px;color:var(--muted)}
.table th{background:var(--orange-soft);color:var(--navy);font-weight:600;text-align:left;height:38px;font-size:11.5px}
.table td{height:44px}
.table tr:nth-child(even) td{background:#f6f6f7}
.table th:first-child,.table td:first-child{padding-left:40px;width:432px}
.table th:nth-child(2),.table td:nth-child(2){width:350px}

/* testimonials */
.testi-bg{left:0;top:3493px;width:1200px;height:448px;background:var(--gray-bg-2)}
.testi{top:3611px;width:240px;height:234px;background:#fff;border-radius:4px;padding:26px 18px 0}
.stars{color:var(--orange);font-size:12px;letter-spacing:2px}
.testi p{font-size:10.5px;line-height:1.75;color:var(--muted);margin-top:6px}
.person{display:flex;align-items:center;gap:10px;margin-top:12px}
.avatar{width:46px;height:46px;border-radius:50%;background:linear-gradient(160deg,#d8c2b4,#8d7a70)}
.person strong{display:block;font-size:15px;color:var(--navy);font-weight:700}
.person span{font-size:11px;color:#2c4f9e;font-weight:500}
.dots{left:0;top:3860px;width:1200px;display:flex;justify-content:center;gap:3px}
.dots i{width:4px;height:4px;border-radius:50%;background:#c9cdd5}
.dots i.on{background:var(--orange)}

/* newsletter */
.news{left:0;top:3941px;width:1200px;height:280px;background:var(--orange);color:#fff}
.news h2{position:absolute;left:141px;top:88px;font-size:29px;font-weight:700}
.news p{position:absolute;left:141px;top:136px;width:400px;font-size:13px;line-height:1.6;color:#fff2e6}
.news-form{position:absolute;left:657px;top:111px;width:400px;height:58px;border-radius:10px;background:rgba(255,255,255,.22);display:flex;overflow:hidden}
.news-form span{flex:1;display:flex;align-items:center;padding-left:22px;font-size:12px;font-weight:500;color:#fff}
.news-form b{width:101px;background:#fff;color:var(--navy);font-size:12px;font-weight:600;display:flex;align-items:center;justify-content:center;border-radius:0 10px 10px 0}

/* footer */
.footer{left:0;top:4221px;width:1200px;height:267px;background:var(--navy);color:#fff}
.footer .brand-name{color:#fff}
.footer .brand-sub{color:#fff}
.foot-about{position:absolute;left:144px;top:134px;width:220px;font-size:9.5px;line-height:1.6;color:#c7cde0}
.foot-col{position:absolute;top:56px}
.foot-col h5{font-size:12.5px;font-weight:600;margin-bottom:14px}
.foot-col li{list-style:none;font-size:10px;color:#c7cde0;margin-bottom:12px}
.contact li{display:flex;align-items:center;gap:8px}
.socials{display:flex;gap:18px;margin-top:4px}
.socials i{width:14px;height:14px;border-radius:50%;background:#fff;display:block}
.copy{position:absolute;left:0;bottom:14px;width:1200px;text-align:center;font-size:9px;color:#c7cde0}
</style>
</head>
<body>

<div class="abs topbar">WELCOME TO CALDER HEALTH – EMPOWERING MENTAL WELLNESS IN DC</div>

<header class="abs header">
  <div class="abs" style="left:141px;top:16px">
    <div class="brand"><span class="brand-dot"></span><span class="brand-name">Calder Health</span></div>
    <div class="brand-sub">SERVICES</div>
  </div>
</header>
<nav class="abs nav">
  <a>Home</a><a class="caret">About Us</a><a class="caret">Services</a><a>Blog</a><a>FAQs</a><a>Contact</a>
</nav>
<a class="abs btn-appt">Make an Appointment</a>

<section class="abs hero">
  <div class="hero-photo" role="img" aria-label="Photo of a smiling young caregiver talking with an elderly man in a bright living room"></div>
  <div class="hero-shade"></div>
  <svg class="hero-wave" width="1200" height="660" viewBox="0 0 1200 660">
    <path d="M0,660 C60,560 220,500 440,510 C700,522 860,560 1010,440 C1090,378 1150,300 1200,250 L1200,280 C1150,330 1090,410 1010,470 C860,585 700,548 440,540 C230,533 80,590 20,660 Z" fill="#f47f20"/>
    <path d="M20,660 C80,590 230,533 440,540 C700,548 860,585 1010,470 C1090,410 1150,330 1200,280 L1200,660 Z" fill="#ffffff"/>
    <circle cx="892" cy="495" r="55" fill="#ffffff" stroke="#f47f20" stroke-width="7"/>
  </svg>
  <h1 class="abs hero-title">Empowering Minds<span class="dot">.</span><br>Restoring Lives<span class="dot">.</span></h1>
  <p class="abs hero-sub">Compassionate, Client-Centered Mental Health Services<br>Tailored For Washington DC's Diverse Communities.</p>
  <a class="abs btn-start">Get Started</a>
</section>

<!-- About -->
<div class="abs about-img-main" role="img" aria-label="Photo of a team of doctors and nurses walking down a hospital corridor"></div>
<div class="abs about-img-small" role="img" aria-label="Photo of a doctor with a stethoscope standing with arms crossed"></div>
<div class="abs label" style="left:610px;top:802px">ABOUT <span class="accent">US</span><span class="mark"><i></i><b></b></span></div>
<h2 class="abs about-title">Your Path to Peaceful<br>Wellness in the <span>Heart of DC</span></h2>
<div class="abs about-text">
  <p>Lorem Ipsum is simply dummy text of the printing and typesetting industry. Lorem Ipsum has been the industry's standard dummy text ever since the 1500s, when an unknown printer took a galley of type and scrambled it to make a type specimen book. It has survived not only five centuries,</p>
  <p>Lorem Ipsum is simply dummy text of the printing and typesetting industry. Lorem Ipsum has been the industry's</p>
  <p>when an unknown printer took a galley of type and scrambled it to make a type specimen book. It has survived not only five centuries, but also the leap into electronic typesetting, remaining essentially unchanged</p>
</div>
<a class="abs read-link navy" style="left:607px;top:1124px">Read More <span>→</span></a>

<!-- Services -->
<div class="abs services-bg"></div>
<div class="abs label center" style="top:1298px">OUR CORE SERVICES<span class="mark"><i></i><b></b></span></div>
<h2 class="abs h2" style="left:0;top:1328px;width:1200px">Your Path to Wellness <span>Starts Here.</span></h2>

<div class="abs svc-card" style="left:141px">
  <div class="svc-img" role="img" aria-label="Photo of a therapist listening to a client in a one-on-one session" style="background:linear-gradient(150deg,#c9c4bb,#7a7d82 60%,#d7d2ca)"></div>
  <div class="svc-icon" style="background:var(--navy)"><svg width="22" height="22" viewBox="0 0 22 22" fill="none" stroke="#f47f20" stroke-width="1.8"><circle cx="11" cy="11" r="7"/><path d="M7 11h8M11 7v8"/></svg></div>
  <div class="svc-title">Individual Therapy</div>
  <div class="svc-text">Lorem Ipsum is simply dummy printing and typesetting industry.</div>
  <a class="read-link orange">Read More <span>→</span></a>
</div>
<div class="abs svc-card" style="left:455px">
  <div class="svc-img" role="img" aria-label="Photo of people seated in a circle during a group session" style="background:linear-gradient(150deg,#d9cfc2,#6b625c 55%,#b7ab9c)"></div>
  <div class="svc-icon" style="background:var(--orange)"><svg width="24" height="22" viewBox="0 0 24 22" fill="none" stroke="#fff" stroke-width="1.8"><circle cx="7" cy="8" r="3"/><circle cx="17" cy="8" r="3"/><path d="M2 19c0-3 2-5 5-5s5 2 5 5M12 19c0-3 2-5 5-5s5 2 5 5"/></svg></div>
  <div class="svc-title">Group Sessions</div>
  <div class="svc-text">Lorem Ipsum is simply dummy printing and typesetting industry.</div>
  <a class="read-link orange">Read More <span>→</span></a>
</div>
<div class="abs svc-card" style="left:770px">
  <div class="svc-img" role="img" aria-label="Photo of clinicians reviewing scans on monitors in a lab" style="background:linear-gradient(150deg,#c5d3df,#4f6f8e 55%,#a9bccd)"></div>
  <div class="svc-icon" style="background:var(--navy)"><svg width="22" height="22" viewBox="0 0 22 22" fill="none" stroke="#fff" stroke-width="1.8"><circle cx="11" cy="7" r="4"/><path d="M4 20c0-4 3-7 7-7s7 3 7 7"/></svg></div>
  <div class="svc-title">Specialized Programs</div>
  <div class="svc-text">Lorem Ipsum is simply dummy printing and typesetting industry.</div>
  <a class="read-link orange">Read More <span>→</span></a>
</div>

<!-- Why choose us -->
<div class="abs label center" style="top:1910px">WHY CHOOSE US<span class="mark"><i></i><b></b></span></div>
<div class="abs why-circle"><div role="img" aria-label="Photo of hands holding a model of a human brain"></div></div>

<div class="abs why-item right" style="left:118px;top:1982px"><h4>Individual Therapy</h4><p>Lorem Ipsum is simply dummy printing<br>and typesetting industry.</p></div>
<div class="abs num n" style="left:391px;top:1989px">1</div>
<div class="abs why-item right" style="left:66px;top:2134px"><h4>Individual Therapy</h4><p>Lorem Ipsum is simply dummy printing<br>and typesetting industry.</p></div>
<div class="abs num o" style="left:337px;top:2140px">3</div>
<div class="abs why-item right" style="left:118px;top:2285px"><h4>Individual Therapy</h4><p>Lorem Ipsum is simply dummy printing<br>and typesetting industry.</p></div>
<div class="abs num n" style="left:391px;top:2292px">5</div>

<div class="abs num n" style="left:769px;top:1989px">2</div>
<div class="abs why-item" style="left:807px;top:1982px"><h4>Individual Therapy</h4><p>Lorem Ipsum is simply dummy printing<br>and typesetting industry.</p></div>
<div class="abs num o" style="left:825px;top:2140px">4</div>
<div class="abs why-item" style="left:862px;top:2134px"><h4>Individual Therapy</h4><p>Lorem Ipsum is simply dummy printing<br>and typesetting industry.</p></div>
<div class="abs num n" style="left:769px;top:2292px">6</div>
<div class="abs why-item" style="left:807px;top:2285px"><h4>Individual Therapy</h4><p>Lorem Ipsum is simply dummy printing<br>and typesetting industry.</p></div>

<div class="abs num o" style="left:588px;top:2365px">7</div>
<div class="abs why-item" style="left:470px;top:2403px;text-align:center"><h4>Individual Therapy</h4><p>Lorem Ipsum is simply dummy printing<br>and typesetting industry.</p></div>

<div class="abs stats">
  <div class="stat"><strong>200+</strong><span>Happy Customer</span></div>
  <div class="stat"><strong>10+</strong><span>Branches</span></div>
  <div class="stat"><strong>43+</strong><span>Doctor Team</span></div>
  <div class="stat"><strong>24/7</strong><span>Available</span></div>
</div>

<!-- Blog -->
<div class="abs label center" style="top:2732px">OUR BLOG<span class="mark"><i></i><b></b></span></div>
<div class="abs blog-track">
  <article class="blog-card feature" style="left:0">
    <h3>Lorem Ipsum Is Simply Dummy Text Of The Printing</h3>
    <p>It is a long established fact that a reader will be distracted by the readable content of a page when looking at its layout. The point of using Lorem Ipsum is that it has a more its layout.</p>
    <a class="read-link orange">Read More <span>→</span></a>
  </article>
  <article class="blog-card" style="left:251px">
    <div class="blog-img" role="img" aria-label="Photo of a man viewing brain scans on screens" style="background:linear-gradient(140deg,#2f4763,#6f8aa6 55%,#1c2d45)"></div>
    <div class="blog-body"><h3>Mind Pain</h3><p>It is a long established fact that a reader will be distracted by the readable content.</p></div>
    <a class="read-link orange">Read More <span>→</span></a>
  </article>
  <article class="blog-card" style="left:502px">
    <div class="blog-img" role="img" aria-label="Photo of a woman outdoors among green trees" style="background:linear-gradient(140deg,#3f5a2f,#7d9a5f 55%,#2c3f24)"></div>
    <div class="blog-body"><h3>Mind Fresh Every Day</h3><p>It is a long established fact that a reader will be distracted by the readable content.</p></div>
    <a class="read-link orange">Read More <span>→</span></a>
  </article>
  <article class="blog-card" style="left:753px">
    <div class="blog-img" role="img" aria-label="Photo of a bright clinic examination room" style="background:linear-gradient(140deg,#e4e4e2,#c4c7c9 55%,#eeeeec)"></div>
    <div class="blog-body"><h3>Lorem Ipsum</h3><p>It is a long established fact that a reader will be distracted by the readable content.</p></div>
    <a class="read-link orange">Read More <span>→</span></a>
  </article>
  <div class="blog-fade"></div>
</div>
<div class="abs arrow" style="left:98px;top:2928px">←</div>
<div class="abs arrow" style="left:1078px;top:2928px">→</div>

<!-- Insurance -->
<div class="abs label center" style="top:3169px">INSURANCE &amp; COST<span class="mark"><i></i><b></b></span></div>
<table class="abs table">
  <thead><tr><th>Accepted Insurers</th><th>Self-Pay Options</th><th>Sliding Scale</th></tr></thead>
  <tbody>
    <tr><td>Keystone Mutual, Harborline, Crestwell</td><td>$150/session</td><td>Available</td></tr>
    <tr><td>Keystone Mutual, Harborline, Crestwell</td><td>$1120/session</td><td>No Available</td></tr>
    <tr><td>Keystone Mutual, Harborline, Crestwell</td><td>$50/session</td><td>Available</td></tr>
    <tr><td>Keystone Mutual, Harborline, Crestwell</td><td>$1140/session</td><td>No Available</td></tr>
  </tbody>
</table>

<!-- Testimonials -->
<div class="abs testi-bg"></div>
<div class="abs label center" style="top:3568px">TESTIMONIALS<span class="mark"><i></i></span></div>
<div class="abs arrow" style="left:143px;top:3716px">←</div>
<div class="abs arrow" style="left:1033px;top:3716px">→</div>
<div class="abs testi" style="left:213px">
  <div class="stars">★★★★</div>
  <p>.. followed by some bogus content. Aenean commodo ligula egget dolor. Aenean massa. Cum sociis natoque penatibus et magnis dis parturient montes, nascetur ridiculus mus.</p>
  <div class="person"><div class="avatar" role="img" aria-label="Client portrait"></div><div><strong>Nora Fields</strong><span>CEO, Company</span></div></div>
</div>
<div class="abs testi" style="left:481px">
  <div class="stars">★★★★</div>
  <p>.. followed by some bogus content. Aenean commodo ligula egget dolor. Aenean massa. Cum sociis natoque penatibus et magnis dis parturient montes, nascetur ridiculus mus.</p>
  <div class="person"><div class="avatar" role="img" aria-label="Client portrait"></div><div><strong>Nora Fields</strong><span>CEO, Company</span></div></div>
</div>
<div class="abs testi" style="left:747px">
  <div class="stars">★★★★</div>
  <p>.. followed by some bogus content. Aenean commodo ligula egget dolor. Aenean massa. Cum sociis natoque penatibus et magnis dis parturient montes, nascetur ridiculus mus.</p>
  <div class="person"><div class="avatar" role="img" aria-label="Client portrait"></div><div><strong>Nora Fields</strong><span>CEO, Company</span></div></div>
</div>
<div class="abs dots"><i class="on"></i><i></i><i></i><i></i><i></i></div>

<!-- Newsletter -->
<section class="abs news">
  <h2>Subcribe to our Newsletter</h2>
  <p>Subscribe for Updates: Stay informed about the latest investor updates, financial results, and announcements by subscribing to our newsletter.</p>
  <div class="news-form"><span>Enter your email</span><b>Subscribe</b></div>
</section>

<!-- Footer -->
<footer class="abs footer">
  <div class="abs" style="left:143px;top:60px">
    <div class="brand"><span class="brand-dot"></span><span class="brand-name">Calder Health</span></div>
    <div class="brand-sub">SERVICES</div>
  </div>
  <p class="foot-about">Lorem Ipsum is simply dummy text of the printing and typesetting industry. Lorem Ipsum has been the industry's standard dummy text ever since the 1500s.</p>
  <div class="foot-col" style="left:498px"><h5>Quick link</h5><ul><li>Home</li><li>About Us</li><li>Services</li><li>Blog</li><li>Contact Us</li></ul></div>
  <div class="foot-col" style="left:695px"><h5>Services</h5><ul><li>Individual Therapy</li><li>Group Sessions</li><li>Specialized Programs</li><li>24/7 Available</li></ul></div>
  <div class="foot-col contact" style="left:932px"><h5>Contact Details</h5><ul>
    <li><svg width="12" height="12" viewBox="0 0 24 24" fill="#f47f20"><path d="M6.6 10.8a15 15 0 006.6 6.6l2.2-2.2a1 1 0 011-.25 11.4 11.4 0 003.6.6 1 1 0 011 1V20a1 1 0 01-1 1A17 17 0 013 4a1 1 0 011-1h3.5a1 1 0 011 1 11.4 11.4 0 00.6 3.6 1 1 0 01-.25 1z"/></svg>(202) 555-0148</li>
    <li><svg width="12" height="10" viewBox="0 0 24 18" fill="#f47f20"><path d="M0 0h24v18H0z"/><path d="M0 0l12 9 12-9" fill="none" stroke="#0d1f44" stroke-width="2"/></svg>hello@calderhealth.com</li>
  </ul><div class="socials"><i></i><i></i><i></i><i></i></div></div>
  <div class="copy">Calder Health © Copyright Northgrid. All Rights Reserved</div>
</footer>

</body>
</html>
```